Förderverein einer Kirchengemeinde sucht Flyer-Design
Zielgruppe
Wir sind ein Förderverein einer Kirchengemeinde, der sich für die kirchenmusikalische Arbeit einsetzt.
Wir wünschen uns ein niveauvolles und zeitgemäßes/modernes Flyerdesign, das die etablierten Konzertbesucher anspricht, aber vor allem auch Menschen erreicht und überzeugt, die (noch) nichts mit Kirche zu tun haben.
Das Alter der (Haupt-) Zielgruppe (Männer und Frauen) erstreckt sich von 45 bis 70 Jahren.
Aufgabenstellung
Bei der Wahl des Formates würden wir (aus der Sicht von Laien) ein zweimal gefaltetes DIN A4 quer Format nehmen. Aber wir lassen uns gerne überraschen und sind grundsätzlich für andere Lösungen offen.
Bitte den Abschnitt für Adress- und sonstige Dateneintragungen samt Kontodaten so gestalten und platzieren, dass man ihn leicht abtrennen und verschicken kann.
Der Flyer soll Kirchenmusik als lebendig und attraktiv darstellen und neue (jüngere) Mitglieder für den Freundeskreis werben.
Lassen Sie die Bilder sprechen!!

```html
<!DOCTYPE html>
<html lang="de">
<head>
<meta charset="utf-8">
<title>Innenseite rechts</title>
<link rel="stylesheet" href="https://fonts.googleapis.com/css2?family=Nunito+Sans:wght@300;400;700&family=Montserrat:wght@300&display=swap">
<style>
  :root {
    --board: #dedede;
    --red-top: #9a1518;
    --red-bottom: #c1191e;
    --white: #ffffff;
    --caption: #2b2b2b;
    --choir-light: #c9b08a;
    --choir-dark: #1c1a1a;
    --organ-light: #d9b368;
    --organ-dark: #17130d;
  }
  html, body {
    margin: 0;
    width: 1200px;
    height: 848px;
    overflow: hidden;
    background: var(--board);
  }
  .board { position: relative; width: 1200px; height: 848px; }
  .page {
    position: absolute;
    left: 137px; top: 88px;
    width: 933px; height: 657px;
    overflow: hidden;
    box-shadow: 2px 3px 5px rgba(0,0,0,0.35);
    font-family: "Nunito Sans", sans-serif;
  }
  .photo-choir {
    position: absolute; left: 0; top: 0; width: 520px; height: 303px;
    background: linear-gradient(180deg, var(--choir-light) 0%, #a88d6c 38%, var(--choir-dark) 62%, #2a2524 100%);
  }
  .photo-organ {
    position: absolute; left: 0; top: 303px; width: 620px; height: 354px;
    background: linear-gradient(125deg, var(--organ-light) 0%, #8a6b33 35%, var(--organ-dark) 65%, #3a3531 100%);
  }
  .panel-shape { position: absolute; left: 0; top: 0; width: 933px; height: 657px; }
  .reasons { position: absolute; inset: 0; color: var(--white); }
  .reasons h2 {
    position: absolute; left: 466px; top: 81px; margin: 0;
    font-size: 20.5px; font-weight: 700; letter-spacing: 0.1px; white-space: nowrap;
  }
  .line {
    position: absolute; margin: 0; white-space: nowrap;
    font-size: 15px; line-height: 18px; font-weight: 300; letter-spacing: 0.4px;
  }
  .caption {
    position: absolute; left: 0; width: 1210px; top: 788px; text-align: center;
    font-family: "Montserrat", sans-serif; font-weight: 300; font-size: 23px;
    letter-spacing: 2px; color: var(--caption); margin: 0;
  }
</style>
</head>
<body>
<div class="board">
  <section class="page">
    <div class="photo-choir" role="img" aria-label="Foto: Chor in schwarzer Kleidung mit Dirigent vor barockem Kirchenaltar"></div>
    <div class="photo-organ" role="img" aria-label="Foto: Hände eines Organisten auf den Tasten einer Orgel"></div>
    <svg class="panel-shape" viewBox="0 0 933 657" aria-hidden="true">
      <defs>
        <linearGradient id="panelRed" x1="0" y1="0" x2="0" y2="1">
          <stop offset="0" stop-color="var(--red-top)"/>
          <stop offset="1" stop-color="var(--red-bottom)"/>
        </linearGradient>
      </defs>
      <polygon points="400,0 414,0 563,657 540,657" fill="#ffffff" opacity="0.28"/>
      <polygon points="414,0 933,0 933,657 563,657" fill="url(#panelRed)"/>
    </svg>
    <div class="reasons">
      <h2>Mitglieder haben gute Gründe:</h2>
      <p class="line" style="left:483px;top:132px">Sie…</p>
      <p class="line" style="left:495px;top:160px">… erhalten ermäßigte Eintrittspreise von</p>
      <p class="line" style="left:518px;top:181px">gemeindeeigenen Konzerten</p>
      <p class="line" style="left:509px;top:221px">… können Konzertkarten vor dem öffentlichen</p>
      <p class="line" style="left:533px;top:242px">Verkauf erwerben</p>
      <p class="line" style="left:524px;top:282px">… gestalten die Arbeit des Freundeskreises</p>
      <p class="line" style="left:548px;top:303px">in den jährlichen Mitgliederversammlungen</p>
      <p class="line" style="left:554px;top:323px">aktiv mit</p>
      <p class="line" style="left:544px;top:364px">… erhalten aktuelle Informationen über</p>
      <p class="line" style="left:568px;top:384px">Veranstaltungen der Gemeinde bequem</p>
      <p class="line" style="left:573px;top:405px">per Email und profitieren so zu allererst</p>
      <p class="line" style="left:565px;top:446px">… können den Mitgliedsbeitrag steuerlich</p>
      <p class="line" style="left:588px;top:466px">absetzen und erhalten eine Spenden-</p>
      <p class="line" style="left:593px;top:486px">bescheinigung</p>
      <p class="line" style="left:584px;top:527px">… können an Ausflügen des</p>
      <p class="line" style="left:609px;top:548px">Freundeskreises teilnehmen</p>
    </div>
  </section>
  <p class="caption">Innenseite rechts</p>
</div>
</body>
</html>
```